Salon and Spa Distributor Business Card

Need a business card. We are are distributor in the salon and spa industry. We identify with natural beauty. Need a card with:
Company Name: Petal Quarry"
Title: "President & CEO"
Address
Company Phone number
email
website
Tag Line:" The Professional Salon Source"

Industry/Entity Type

Business

Contact Information for Business Card

Name: Dov Strommen
Title: "President & CEO"
Address: 31 Harlow Ln, Bexmoor, NJ 07813
Company Phone number: 800-463-5918
email: dovstrommen@petalquarry.example
website: www.petalquarry.example

Requirements
Should not have
• No black backgrounds

```html
<!DOCTYPE html>
<html lang="en">
<head>
<meta charset="utf-8">
<title>Petal Quarry Business Card</title>
<link rel="stylesheet" href="https://fonts.googleapis.com/css2?family=Questrial&display=swap">
<style>
  :root {
    --stage: #000000;
    --card-white: #ffffff;
    --brand-green: #2f8f34;
    --deep-green: #1f6e2a;
    --text-dark: #1a1a1a;
    --mark-green: #5cb848;
    --back-top: #3f8d4f;
    --back-bottom: #0b6a34;
  }
  html, body {
    margin: 0;
    padding: 0;
    width: 1200px;
    height: 900px;
    overflow: hidden;
    background: var(--stage);
    font-family: "Questrial", "Century Gothic", sans-serif;
  }
  .stage { position: relative; width: 1200px; height: 900px; }
  .card {
    position: absolute;
    top: 271px;
    width: 457px;
    height: 281px;
    overflow: hidden;
  }
  .card-front { left: 137px; background: var(--card-white); }
  .card-back {
    left: 626px;
    background: linear-gradient(180deg, var(--back-top) 0%, var(--back-bottom) 100%);
  }
  .holder-name {
    position: absolute; left: 28px; top: 24px; margin: 0;
    font-size: 22px; font-weight: 400; letter-spacing: 0.5px;
    color: var(--brand-green); text-transform: uppercase;
  }
  .holder-title {
    position: absolute; left: 28px; top: 50px; margin: 0;
    font-size: 13px; color: var(--text-dark);
  }
  .tagline {
    position: absolute; top: 28px; left: 0; margin: 0;
    font-size: 14px; color: var(--deep-green); line-height: 17px;
  }
  .tagline span { display: block; }
  .tagline .t1 { padding-left: 302px; }
  .tagline .t2 { padding-left: 315px; }
  .tagline .t3 { padding-left: 362px; }
  .tagline .t4 { padding-left: 381px; }
  .brand-front {
    position: absolute; left: 28px; top: 100px;
    display: flex; align-items: center; gap: 14px;
  }
  .brand-dot {
    width: 58px; height: 58px; border-radius: 50%;
    background: var(--mark-green);
  }
  .brand-name {
    font-size: 22px; color: var(--brand-green);
  }
  .contacts {
    position: absolute; left: 28px; top: 200px; margin: 0; padding: 0;
    list-style: none; font-size: 14px; color: var(--text-dark); line-height: 17px;
  }
  .contacts li { display: flex; align-items: center; gap: 6px; }
  .contacts svg { width: 10px; height: 10px; fill: var(--brand-green); }
  .address {
    position: absolute; right: 29px; top: 201px; margin: 0;
    font-size: 14px; line-height: 17px; color: var(--text-dark);
    text-align: right; font-style: normal;
  }
  .brand-back {
    position: absolute; left: 0; right: 0; top: 114px; margin: 0;
    text-align: center; font-size: 40px; font-weight: 400;
    color: var(--card-white);
  }
</style>
</head>
<body>
<div class="stage">
  <section class="card card-front">
    <h1 class="holder-name">Dov Strommen</h1>
    <p class="holder-title">President &amp; CEO</p>
    <p class="tagline">
      <span class="t1">The</span>
      <span class="t2">Professional</span>
      <span class="t3">Salon</span>
      <span class="t4">Source</span>
    </p>
    <div class="brand-front">
      <div class="brand-dot"></div>
      <span class="brand-name">Petal Quarry</span>
    </div>
    <ul class="contacts">
      <li>
        <svg viewBox="0 0 10 10" aria-hidden="true"><path d="M1 3 Q5 0 9 3 L8 4.5 L6.5 3.8 L6.5 3 Q5 2.5 3.5 3 L3.5 3.8 L2 4.5 Z M2.5 5 L7.5 5 L8.5 9 L1.5 9 Z"/></svg>
        800-463-5918
      </li>
      <li>
        <svg viewBox="0 0 10 10" aria-hidden="true"><path d="M0.5 2 L9.5 2 L9.5 8.5 L0.5 8.5 Z M1.3 2.8 L5 5.6 L8.7 2.8 Z" fill-rule="evenodd"/></svg>
        dovstrommen@petalquarry.example
      </li>
      <li>
        <svg viewBox="0 0 10 10" aria-hidden="true"><circle cx="5" cy="5" r="4.5"/></svg>
        www.petalquarry.example
      </li>
    </ul>
    <address class="address">31 Harlow Ln,<br>Bexmoor,<br>NJ 07813</address>
  </section>

  <section class="card card-back">
    <h2 class="brand-back">Petal Quarry</h2>
  </section>
</div>
</body>
</html>
```